Business card for my new company (Accounting firm)

I need a business card for my new business Brightwell Advisory and Ledger SA. Our services are accounting, tax, audit and financial management. Our customers are small companies, start-ups and new companies. The final design has to show financial security, trust and growth. Please find our logo attached to the business card. Text for the business card: Brightwell Advisory and Ledger SA Tomas Varenholt Director and Founder Certified Accountant Tel. 022 418 57 34 tv@clairevalconseil.ch www.clairevalconseil.ch Rue des Vergières 27 1201 Geneva
Target Market(s)
Our customers are small companies, start-ups and new companies.
Industry/Entity Type
Finance And Accounting
Contact Information for Business Card
Claireval Conseil et Comptes SA
Tomas Varenholt
Directeur et Fondateur
Expert-comptable diplômé
Tél. 022 418 57 34
tv@clairevalconseil.ch
www.clairevalconseil.ch
Rue des Vergières 27
1201 Genève

```html
<!DOCTYPE html>
<html lang="en">
<head>
<meta charset="utf-8">
<title>Claireval Conseil et Comptes SA – Business Card</title>
<link href="https://fonts.googleapis.com/css2?family=Lato:wght@400;700&display=swap" rel="stylesheet">
<style>
  :root {
    --backdrop: #1c1c1e;
    --blue-deep: #1a78b9;
    --blue-bright: #33b3e6;
    --blue-accent: #2aa3df;
    --ink: #4a4a4e;
    --ink-soft: #5c5c60;
    --paper: #ffffff;
    --divider: #d6d6d8;
  }
  * { margin: 0; padding: 0; box-sizing: border-box; }
  html, body {
    width: 1200px; height: 900px; overflow: hidden;
    background: var(--backdrop);
    font-family: "Lato", Arial, sans-serif;
  }
  .canvas { position: relative; width: 1200px; height: 900px; }

  .card {
    position: absolute;
    width: 540px; height: 320px;
    border-radius: 2px;
    box-shadow: 0 12px 30px rgba(0,0,0,0.5);
  }

  /* Front (blue) side */
  .card--front {
    left: 90px; top: 100px;
    background: radial-gradient(ellipse at 60% 35%, var(--blue-bright) 0%, #2a9ad6 45%, var(--blue-deep) 100%);
    color: var(--paper);
  }
  .front-brand {
    position: absolute; left: 0; right: 0; top: 100px;
    display: flex; align-items: center; justify-content: center; gap: 14px;
    font-size: 30px; font-weight: 700; letter-spacing: 1px;
  }
  .front-brand .brand-square { width: 22px; height: 22px; background: var(--paper); }
  .front-web {
    position: absolute; left: 0; right: 0; bottom: 44px;
    text-align: center; font-size: 15px; letter-spacing: 3px;
  }

  /* Back (white) side */
  .card--back {
    left: 570px; top: 480px;
    background: var(--paper);
    display: flex;
  }
  .back-brand {
    width: 250px;
    display: flex; flex-direction: column; justify-content: center; align-items: flex-start;
    padding-left: 36px; gap: 12px;
  }
  .back-brand .brand-square { width: 34px; height: 34px; background: var(--blue-accent); }
  .back-brand .brand-name {
    font-size: 22px; font-weight: 700; color: var(--ink); line-height: 1.2;
  }
  .divider { width: 1px; margin: 40px 0; background: var(--divider); }
  .contact {
    padding: 52px 0 0 26px;
    color: var(--ink-soft); font-size: 15px; line-height: 1.3;
  }
  .contact-name {
    color: var(--blue-accent); font-weight: 700; font-size: 17px; letter-spacing: 0.3px;
  }
  .contact-roles { margin-bottom: 10px; }
  .contact-line { display: flex; align-items: center; gap: 8px; }
  .contact-line svg { width: 13px; height: 13px; flex: none; }
  .contact-address { margin-top: 10px; }
</style>
</head>
<body>
<main class="canvas">
  <section class="card card--front" aria-label="Card front">
    <div class="front-brand"><span class="brand-square"></span><span>Claireval</span></div>
    <p class="front-web">www.clairevalconseil.ch</p>
  </section>

  <section class="card card--back" aria-label="Card back">
    <div class="back-brand">
      <span class="brand-square"></span>
      <span class="brand-name">Claireval Conseil<br>et Comptes SA</span>
    </div>
    <div class="divider"></div>
    <div class="contact">
      <p class="contact-name">SA TOMAS VARENHOLT</p>
      <p class="contact-roles">Director and Founder<br>Certified Accountant</p>
      <p class="contact-line">
        <svg viewBox="0 0 16 16" aria-hidden="true"><path fill="#2aa3df" d="M3 2h3l1 3-2 1c1 2 2 3 4 4l1-2 3 1v3c0 1-1 2-2 2C6 14 2 10 2 4c0-1 0-2 1-2z"/></svg>
        022 418 57 34
      </p>
      <p class="contact-line">
        <svg viewBox="0 0 16 16" aria-hidden="true"><rect x="1" y="3" width="14" height="10" fill="#2aa3df"/><path d="M1 3l7 6 7-6" stroke="#fff" stroke-width="1.4" fill="none"/></svg>
        tv@clairevalconseil.ch
      </p>
      <p class="contact-line">
        <svg viewBox="0 0 16 16" aria-hidden="true"><circle cx="8" cy="8" r="7" fill="#2aa3df"/><path d="M1 8h14M8 1c-3 4-3 10 0 14M8 1c3 4 3 10 0 14" stroke="#fff" stroke-width="1" fill="none"/></svg>
        www.clairevalconseil.ch
      </p>
      <p class="contact-address">Rue des Vergières 27<br>1201 Geneva</p>
    </div>
  </section>
</main>
</body>
</html>
```